Music Studio and Store Business Card and Logo Design

We need a business card and logo design for an existing Music Studio (Piano and Voice) which will soon expand to offer retail sheet music for all instruments including voice. The expanding store will not sell or lease instruments. We are a well known Fine Arts Studio for instruction to children, college students, and adults with 42 enrolled students and a wait list. We want something with simple elegance, but not archaic. Even a sleek modern look is okay. We do not want something childish or too fun looking because we do serve ages 5 - 62. We would also like the logo workable/transferable to signage for our new location opening in March. We like classic burgundy, black, deep blues, but are open to other suggestions. We included our studio brochure so you can get to know us a little better and some images we thought were interesting with the use of clef signs for the & and using note heads for the bottom or top of the letter "H"

Target Market(s)

All ages

Industry/Entity Type

Business

Contact Information for Business Card

H&H Music StudioPlattsburgh, NYWanda J. Haby and Oren M. Castaldi, Owners

Requirements
Must have
• Phone Number: (555) 817-4062
• Website: www.rbtonalartsroom.example
Nice to have
• Email: lorna@rbtonalartsroom.example
Should not have
• Any instruments on the card other than piano. Instrument pix is not a necessity.

```html
<!DOCTYPE html>
<html lang="en">
<head>
<meta charset="utf-8">
<title>R&amp;B Music Studio – Business Card</title>
<link rel="stylesheet" href="https://fonts.googleapis.com/css2?family=Open+Sans:wght@400;600&display=swap">
<style>
  :root {
    --page-bg: #e6e4e2;
    --card-bg: #f8f8f8;
    --card-edge: #ffffff;
    --accent-red: #e8141c;
    --ink: #1a1a1a;
    --mark-black: #111111;
  }
  * { margin: 0; padding: 0; box-sizing: border-box; }
  html, body {
    width: 1200px;
    height: 900px;
    overflow: hidden;
    background: var(--page-bg);
    font-family: "Open Sans", Arial, sans-serif;
  }
  .business-card {
    position: absolute;
    left: 150px;
    top: 175px;
    width: 900px;
    height: 551px;
    background: var(--card-bg);
    border: 3px solid var(--card-edge);
    border-radius: 20px;
    box-shadow: 0 10px 30px rgba(0,0,0,0.12);
  }
  .brand {
    position: absolute;
    left: 370px;
    top: 90px;
    display: flex;
    align-items: center;
    gap: 22px;
  }
  .brand-dot {
    width: 120px;
    height: 120px;
    border-radius: 50%;
    background: var(--mark-black);
  }
  .brand-name {
    font-family: "Open Sans", Arial, sans-serif;
    font-weight: 600;
    font-size: 29px;
    color: var(--accent-red);
    white-space: nowrap;
  }
  .owners {
    position: absolute;
    left: 46px;
    top: 250px;
  }
  .owner-name {
    font-weight: 600;
    font-size: 29px;
    line-height: 36px;
    color: var(--accent-red);
  }
  .owner-role {
    font-size: 24px;
    line-height: 34px;
    color: var(--ink);
  }
  .address {
    position: absolute;
    left: 46px;
    top: 412px;
  }
  .address-label {
    font-weight: 600;
    font-size: 27px;
    line-height: 38px;
    color: var(--accent-red);
  }
  .address-city {
    font-size: 23px;
    line-height: 34px;
    color: var(--ink);
  }
  .contact {
    position: absolute;
    right: 46px;
    top: 416px;
    text-align: right;
  }
  .contact-line {
    font-size: 23px;
    line-height: 34px;
    color: var(--ink);
    white-space: nowrap;
  }
</style>
</head>
<body>
  <div class="business-card">
    <div class="brand">
      <div class="brand-dot"></div>
      <div class="brand-name">R&amp;B Music Studio</div>
    </div>

    <div class="owners">
      <div class="owner-name">Lorna P. Quist</div>
      <div class="owner-name">Oren M. Castaldi</div>
      <div class="owner-role">Owners</div>
    </div>

    <div class="address">
      <div class="address-label">Address</div>
      <div class="address-city">Alder Falls, NY</div>
    </div>

    <div class="contact">
      <div class="contact-line">(555) 817-4062</div>
      <div class="contact-line">www.rbtonalartsroom.example</div>
    </div>
  </div>
</body>
</html>
```